Pressure Washing Hog Confinements

We clean and disinfect Hog confinements in-order to receive new pigs.

Needs to emphasis Clean Healthy barns (pigs), work done in timely manner, 100% satisfied, Bio-security rules followed. I do not have specific colors, no logo's.

Contact Information will be sent once design is agreed on.
Business Name - Brandt & Daughters Power Washing
Phone Number - Send latter
E-mail - Send latter
Web Address - Send latter

Target Market(s)

Farmers

Industry/Entity Type

Business

Requirements
Must have
• We are Insured
Bio-Security
100% Satisfied
Water Conservation

Size - 2 sided Postcard 8.5" x 5.5"
Nice to have
• I want to emphasize healthy and happy pigs because of a quality job done. Picture of pigs dose not need to be used but may be just an example.

Also attached is picture of a barn I would like to see used. on the back side. Every owner seeing this will know this is a hog barn and have an idea what we do.

```html
<!DOCTYPE html>
<html lang="en">
<head>
<meta charset="utf-8">
<title>Brandt &amp; Daughters Power Washing – Postcard</title>
<link href="https://fonts.googleapis.com/css2?family=Allura&family=Arimo:wght@400;700&family=Open+Sans:wght@700&display=swap" rel="stylesheet">
<style>
  :root {
    --maroon: #8b4247;
    --orange: #f2a845;
    --charcoal: #3b3b3d;
    --white: #ffffff;
    --ink: #1f1f1f;
    --backdrop: #7a5a41;
    --photo-top: #8fbde6;
    --photo-bottom: #d6d8da;
  }
  * { box-sizing: border-box; margin: 0; padding: 0; }
  html, body { width: 1200px; height: 572px; overflow: hidden; background: var(--backdrop); }
  .stage { position: relative; width: 1200px; height: 572px; overflow: hidden; background: var(--backdrop); font-family: "Arimo", Arial, sans-serif; }

  .side-label {
    position: absolute; top: 36px; width: 574px; text-align: center;
    color: var(--white); font-family: "Arimo", Arial, sans-serif; font-weight: 400; font-size: 40px; letter-spacing: 4px;
  }
  .side-label--front { left: 17px; }
  .side-label--back { left: 611px; }

  .card {
    position: absolute; top: 112px; width: 612px; height: 396px;
    transform: scale(0.9375); transform-origin: top left;
    overflow: hidden; box-shadow: 0 2px 8px rgba(0,0,0,.35);
  }
  .card--front { left: 17px; background: var(--maroon); }
  .card--back { left: 611px; background: var(--white); }

  /* Front */
  .front-shapes { position: absolute; inset: 0; }
  .front-title {
    position: absolute; left: 16px; top: 14px;
    font-family: "Allura", cursive; font-weight: 400; font-size: 56px; line-height: 1.1;
    color: var(--orange); white-space: nowrap;
  }
  .front-service {
    position: absolute; left: 0; right: 0; top: 339px; text-align: center;
    font-family: "Open Sans", Arial, sans-serif; font-weight: 700; font-size: 14.5px; color: var(--ink);
  }
  .front-tagline {
    position: absolute; left: 0; right: 0; bottom: 0; height: 31px;
    background: var(--charcoal); color: var(--white); font-weight: 400;
    font-size: 17px; letter-spacing: 0.6px; line-height: 31px; text-align: center; text-transform: uppercase;
  }

  /* Back */
  .back-panel { position: absolute; left: 0; top: 0; width: 300px; height: 396px; background: var(--maroon); }
  .back-heading { position: absolute; left: 15px; top: 24px; color: var(--orange); font-weight: 400; font-size: 20.5px; }
  .benefit-list { position: absolute; left: 13px; top: 50px; list-style: none; }
  .benefit-list li { color: var(--white); font-size: 21px; line-height: 27.5px; white-space: nowrap; }
  .benefit-list li::before { content: "•"; color: var(--orange); margin-right: 3px; }
  .back-name {
    position: absolute; left: 18px; top: 280px;
    font-family: "Allura", cursive; font-weight: 400; font-size: 29px; color: var(--orange); white-space: nowrap;
  }
  .contact { position: absolute; left: 20px; color: var(--white); font-size: 14.5px; }
  .contact b { color: var(--orange); font-weight: 400; font-size: 16px; margin-right: 8px; }
  .contact--phone { top: 318px; }
  .contact--email { top: 339px; }
  .back-web {
    position: absolute; left: 0; bottom: 0; width: 300px; height: 31px;
    background: var(--charcoal); color: var(--white); font-size: 14.5px; line-height: 31px; padding-left: 19px;
  }
  .return-address { position: absolute; left: 324px; top: 22px; font-size: 9.5px; line-height: 12.5px; color: var(--ink); font-style: normal; }
  .return-address strong { font-weight: 700; }
  .indicia {
    position: absolute; left: 529px; top: 32px; width: 54px; height: 54px;
    border: 1px solid var(--ink); text-align: center; font-size: 6.2px; line-height: 8px; padding-top: 3px; color: var(--ink);
  }
  .indicia .paid { font-size: 8px; }
  .recipient {
    position: absolute; left: 475px; top: 101px; width: 108px; height: 55px;
    border: 1px solid var(--ink); font-size: 9.5px; line-height: 12px; padding: 16px 0 0 12px; color: var(--ink);
  }
  .address-line { position: absolute; left: 343px; width: 237px; height: 0; border-top: 1.5px solid var(--ink); }
</style>
</head>
<body>
<main class="stage">
  <p class="side-label side-label--front">front</p>
  <p class="side-label side-label--back">back</p>

  <section class="card card--front" aria-label="Postcard front">
    <svg class="front-shapes" width="612" height="396" viewBox="0 0 612 396">
      <defs>
        <linearGradient id="sweep" x1="0" y1="0" x2="1" y2="0">
          <stop offset="0" stop-color="#ffffff"/>
          <stop offset="1" stop-color="#ffffff" stop-opacity="0"/>
        </linearGradient>
        <linearGradient id="photoTone" x1="0" y1="0" x2="0" y2="1">
          <stop offset="0" stop-color="var(--photo-top)"/>
          <stop offset="1" stop-color="var(--photo-bottom)"/>
        </linearGradient>
      </defs>
      <polygon points="0,134 612,80 612,365 0,365" fill="url(#photoTone)" role="img" aria-label="Photo of a hog confinement barn with grain silos under a blue sky"/>
      <polygon points="0,96 600,66 0,124" fill="url(#sweep)"/>
    </svg>
    <h1 class="front-title">Brandt and Daughters</h1>
    <p class="front-service">We clean and disinfect Hog confinements in-order to receive new pigs</p>
    <p class="front-tagline">Healthy and happy pigs because of a quality job done</p>
  </section>

  <section class="card card--back" aria-label="Postcard back">
    <div class="back-panel">
      <h2 class="back-heading">WE ARE INSURED</h2>
      <ul class="benefit-list">
        <li>Clean Healthy barns</li>
        <li>Work done in timely manner</li>
        <li>100% satisfied</li>
        <li>Bio-security</li>
        <li>Water conservation</li>
      </ul>
      <p class="back-name">Brandt &amp; Daughters</p>
      <p class="contact contact--phone"><b>P :</b>555-014-2290</p>
      <p class="contact contact--email"><b>E :</b>info@brandtanddaughters.com</p>
      <p class="back-web">www.brandtanddaughters.com</p>
    </div>
    <address class="return-address">
      <strong>Return Address</strong><br>
      Brandt &amp; Daughters<br>
      Street Name, City Name<br>
      State Zip Code
    </address>
    <div class="indicia">PRSRT STD<br>ECRWSS<br>U.S.POSTAGE<br><span class="paid">PAID</span><br>EDDM Retail</div>
    <div class="recipient">Local<br>Postal Customer</div>
    <span class="address-line" style="top:224px"></span>
    <span class="address-line" style="top:254px"></span>
    <span class="address-line" style="top:284px"></span>
    <span class="address-line" style="top:314px"></span>
  </section>
</main>
</body>
</html>
```